Tutoring Site Hero Image Design

Updated Hero Concept for BrightHarborLessons.com

Create a hero that communicates “high quality, in-person private tutoring for all ages,” with warmth, credibility, and a real-life feel. The hero should move away from generic stock photography and better reflect the moments that make our service different: tutors meeting students where they are, one-on-one engagement, and a range of ages.

What the New Hero Should Convey
1. In-person, private, one-on-one support
This is the core differentiator, so the visual should feel intimate, focused, and real. Avoid anything that resembles online learning settings or learning-center classrooms.

2. Coverage of age ranges without clutter
We serve elementary through college. We do not need multiple students in the hero, but the chosen student should not skew strongly to one age group. Aim for a middle-ground age that feels inclusive, for example a middle schooler or early high schooler.

3. Realistic, authentic moments
Use photography that feels candid and warm. Natural light, home settings, kitchen tables, quiet study nooks, or library corners work well. Avoid staged stock looks, harsh lighting, or exaggerated classroom setups.

Design the hero at 2400 × 1200 px, with the focal point on the right side, safe area leaving room on the left for a stacked headline and form.

Images that I've shared as just thought starters and do not need to be used in the design.

Font styles to use
Sans Serif

Colors
0054AA
0677BA
7BADD7
CADEEF
E8F1F8
EB3D1F
EC4F4E
F09395
F8D3D4
FCEDEE
6B429C
8869AF
B7A5CE
E3DAEB
F3F0F8

```html
<!DOCTYPE html>
<html lang="en">
<head>
<meta charset="UTF-8">
<title>Bright Harbor – Local Tutors</title>
<link rel="stylesheet" href="https://fonts.googleapis.com/css2?family=Arimo:wght@400;700&family=Lexend:wght@500&display=swap">
<style>
  :root {
    --page-bg: #dddddd;
    --navy: #0b2385;
    --navy-deep: #08196b;
    --ring: #3e55a6;
    --white: #ffffff;
    --field-fill: rgba(255, 255, 255, 0.1);
    --red: #e4002b;
    --tear-red: #d0102f;
    --photo-warm: #b07a4a;
    --photo-grey: #a9a7a1;
    --photo-light: #d9d8d3;
  }
  * { margin: 0; padding: 0; box-sizing: border-box; }
  html, body {
    width: 1200px;
    height: 670px;
    overflow: hidden;
    background: var(--page-bg);
  }
  .hero {
    position: absolute;
    left: 64px;
    top: 67px;
    width: 1071px;
    height: 536px;
    overflow: hidden;
    background: radial-gradient(ellipse at 30% 40%, var(--navy) 0%, var(--navy-deep) 100%);
    font-family: "Arimo", Arial, sans-serif;
    color: var(--white);
  }
  .brand-badge {
    position: absolute;
    left: 72px;
    top: -100px;
    width: 176px;
    height: 176px;
    border-radius: 50%;
    background: var(--ring);
    opacity: 0.9;
  }
  .brand-disc {
    position: absolute;
    left: 82px;
    top: -90px;
    width: 156px;
    height: 156px;
    border-radius: 50%;
    background: var(--white);
  }
  .brand {
    position: absolute;
    left: 104px;
    top: 12px;
    display: flex;
    align-items: center;
    gap: 8px;
  }
  .brand-dot {
    width: 12px;
    height: 12px;
    border-radius: 50%;
    background: var(--red);
  }
  .brand-name {
    font-family: "Lexend", Arial, sans-serif;
    font-weight: 500;
    font-size: 16px;
    line-height: 15px;
    color: var(--navy);
  }
  .headline {
    position: absolute;
    left: 42px;
    top: 98px;
    font-weight: 700;
    line-height: 1;
    letter-spacing: 0.5px;
  }
  .headline-lead { display: block; font-size: 61px; }
  .headline-sub { display: block; font-size: 48px; margin-top: 4px; }
  .headline-sub + .headline-sub { margin-top: 1px; }
  .audience {
    position: absolute;
    left: 44px;
    top: 269px;
    width: 364px;
    list-style: none;
  }
  .audience-option {
    height: 43px;
    margin-bottom: 14px;
    border: 1.5px solid var(--white);
    border-radius: 22px;
    background: var(--field-fill);
    padding-left: 31px;
    display: flex;
    align-items: center;
    font-size: 15px;
  }
  .cta {
    position: absolute;
    left: 44px;
    top: 440px;
    width: 165px;
    height: 42px;
    border-radius: 21px;
    background: var(--red);
    display: flex;
    align-items: center;
    justify-content: center;
    font-weight: 700;
    font-size: 18px;
  }
  .photo-area {
    position: absolute;
    left: 0;
    top: 0;
    width: 1071px;
    height: 536px;
  }
</style>
</head>
<body>
  <section class="hero">
    <svg class="photo-area" viewBox="0 0 1071 536" width="1071" height="536">
      <defs>
        <linearGradient id="photoTone" x1="0" y1="0" x2="0" y2="1">
          <stop offset="0" stop-color="var(--photo-light)"/>
          <stop offset="0.5" stop-color="var(--photo-grey)"/>
          <stop offset="0.78" stop-color="var(--photo-warm)"/>
          <stop offset="1" stop-color="#8f5f36"/>
        </linearGradient>
      </defs>
      <path class="tear-edge" fill="var(--tear-red)"
        d="M570 0 L1071 0 L1071 536 L505 536 L500 520 L510 500 L497 480 L505 455 L493 430 L503 405 L495 380 L500 350 L490 325 L484 300 L495 278 L488 255 L503 230 L507 205 L494 180 L500 150 L492 118 L510 95 L518 70 L535 48 L548 25 Z"/>
      <path role="img" aria-label="Photo: a tutor and a young student writing together at a wooden kitchen table with books"
        fill="url(#photoTone)"
        d="M578 0 L1071 0 L1071 536 L514 536 L510 518 L519 499 L507 480 L514 455 L503 430 L512 405 L505 380 L509 350 L500 325 L496 300 L505 278 L498 255 L513 230 L517 205 L505 180 L510 150 L503 118 L520 95 L528 70 L544 48 L556 25 Z"/>
    </svg>

    <div class="brand-badge"></div>
    <div class="brand-disc"></div>
    <div class="brand">
      <span class="brand-dot"></span>
      <span class="brand-name">Bright<br>Harbor</span>
    </div>

    <h1 class="headline">
      <span class="headline-lead">Local Tutors.</span>
      <span class="headline-sub">1-on-1 Learning.</span>
      <span class="headline-sub">Real Results.</span>
    </h1>

    <ul class="audience">
      <li class="audience-option">Your Child</li>
      <li class="audience-option">Yourself</li>
      <li class="audience-option">Someone else</li>
    </ul>

    <div class="cta">Get a Quote</div>
  </section>
</body>
</html>
```